Lawn sign for construction company

Would like this to be a very clean and high end design for luxury homes. We need a yard sign designed that includes the company logo, website, phone number and major service offerings (residential and commercial renovations and maintenance)
The company website is brackwellbuilders.com all other contact info is in the attachments
Target Market(s)
Luxury home owners and business owners
Industry/Entity Type
Construction/Home Improvement
Font styles to use
Other font styles liked:
- See company logo and other graphics included for title text fonts. All other fonts can be standard sans serif.
Colors
0054AA
0677BA
7BADD7
CADEEF
E8F1F8
Requirements
Must have
- Clean, easy to read design, would like 2 sided sign. A main sign side and back side which states “free estimates, and includes the website and phone number. Must also match the color scheme of the provided logo and other company images. Dark Navy blue primary color, gray secondary color, and orange as an accent color.
Nice to have
- 2nd sign side very simple design
Should not have
- Too many graphics limit to 1-3 colors

```html
<!DOCTYPE html>
<html lang="en">
<head>
<meta charset="utf-8">
<title>Brackwell Construction Company – Yard Sign</title>
<link href="https://fonts.googleapis.com/css2?family=Montserrat:wght@500;600;700;800;900&display=swap" rel="stylesheet">
<style>
  :root{
    --navy:#0b0a5f;
    --orange:#f07a0c;
    --gray:#6e6e6e;
    --white:#ffffff;
    --paper:#f4f4f4;
    --stage-dark:#3a3a3a;
    --stage-light:#9d9d9d;
  }
  *{margin:0;padding:0;box-sizing:border-box;}
  html,body{width:1200px;height:2355px;overflow:hidden;}
  body{
    position:relative;
    font-family:"Montserrat",sans-serif;
    background:linear-gradient(90deg,var(--stage-dark) 0%,var(--stage-light) 100%);
  }

  /* side labels */
  .side-label{
    position:absolute;
    color:var(--white);
    font-weight:600;
    font-size:58px;
    letter-spacing:1px;
    transform:rotate(-90deg);
    transform-origin:center;
    white-space:nowrap;
  }
  .side-label--front{left:30px;top:1330px;width:140px;text-align:center;}
  .side-label--back{left:35px;top:1995px;width:140px;text-align:center;}

  /* sign panels */
  .sign{
    position:absolute;
    width:718px;height:574px;
    box-shadow:0 14px 18px rgba(0,0,0,.25);
    overflow:hidden;
  }
  .sign__frame{position:absolute;inset:22px;border:3px solid var(--navy);}
  .sign__frame-inner{position:absolute;inset:34px;border:1.5px solid var(--navy);}

  .sign--front{
    background:linear-gradient(160deg,#ffffff 0%,var(--paper) 45%,#ffffff 60%,#ececec 100%);
  }
  .sign--hero{left:200px;top:145px;transform:scale(1.22);transform-origin:top left;}
  .sign--front-flat{left:241px;top:1077px;}

  /* company name block, filling the logo area */
  .brand{
    position:absolute;left:0;right:0;top:52px;height:268px;
    display:flex;align-items:center;justify-content:center;gap:26px;
  }
  .brand__dot{width:130px;height:130px;border-radius:50%;background:var(--gray);flex:none;}
  .brand__name{
    color:var(--orange);
    font-weight:800;
    font-size:48px;
    line-height:1.04;
    text-align:left;
    letter-spacing:.5px;
  }
  .brand__name .brand__sub{display:block;font-size:24px;letter-spacing:18px;margin-top:6px;}

  .banner-art{position:absolute;left:0;top:0;width:718px;height:574px;}

  .services{
    position:absolute;left:0;right:0;top:370px;
    text-align:center;color:var(--navy);
    font-size:26px;line-height:36px;font-weight:800;
  }
  .services .joiner{font-weight:500;}

  /* back side */
  .sign--back{left:241px;top:1730px;background:var(--navy);}
  .sign--back .sign__frame,.sign--back .sign__frame-inner{border-color:var(--white);}
  .back__tag{
    position:absolute;left:0;right:0;top:80px;text-align:center;
    color:var(--white);font-weight:800;font-size:25px;letter-spacing:4.5px;
  }
  .ribbon{
    position:absolute;left:90px;width:545px;
    background:var(--white);
    transform:rotate(-4deg);
    color:var(--orange);font-weight:800;
    display:flex;align-items:center;justify-content:center;
    box-shadow:0 22px 18px -10px rgba(60,60,200,.35);
    white-space:nowrap;
  }
  .ribbon--estimates{top:148px;height:84px;font-size:55px;letter-spacing:.5px;}
  .ribbon--phone{top:253px;height:90px;font-size:74px;letter-spacing:-1.5px;}
  .back__web{
    position:absolute;left:0;right:0;top:389px;text-align:center;
    color:var(--white);font-weight:600;font-size:34px;letter-spacing:1px;
  }
  .back__address{
    position:absolute;left:0;right:0;top:452px;text-align:center;
    color:var(--white);font-weight:500;font-size:22px;line-height:32px;
  }
</style>
</head>
<body>

  <!-- front side, large view -->
  <section class="sign sign--front sign--hero" aria-label="Sign front">
    <div class="sign__frame"></div>
    <div class="sign__frame-inner"></div>
    <div class="brand">
      <div class="brand__dot"></div>
      <div class="brand__name">BRACKWELL<br>CONSTRUCTION<span class="brand__sub">COMPANY</span></div>
    </div>
    <svg class="banner-art" viewBox="0 0 718 574" aria-hidden="true">
      <path d="M150 300 Q128 330 128 362 L140 362 Q142 330 160 302 Z" fill="var(--navy)"/>
      <path d="M568 300 Q590 330 590 362 L578 362 Q576 330 558 302 Z" fill="var(--navy)"/>
      <path d="M150 530 Q128 500 128 468 L140 468 Q142 500 160 528 Z" fill="var(--navy)"/>
      <path d="M568 530 Q590 500 590 468 L578 468 Q576 500 558 528 Z" fill="var(--navy)"/>
      <polygon points="92,335 640,335 662,400 640,468 92,468 70,400" fill="var(--white)" stroke="var(--navy)" stroke-width="5" stroke-linejoin="round"/>
      <polygon points="60,400 88,392 84,400 88,408" fill="var(--navy)"/>
      <polygon points="672,400 644,392 648,400 644,408" fill="var(--navy)"/>
    </svg>
    <div class="services">
      RESIDENTIAL <span class="joiner">AND</span> COMMERCIAL<br>
      RENOVATIONS <span class="joiner">AND</span> MAINTENANCE
    </div>
  </section>

  <div class="side-label side-label--front">FRONT</div>
  <div class="side-label side-label--back">BACK</div>

  <!-- front side -->
  <section class="sign sign--front sign--front-flat" aria-label="Sign front">
    <div class="sign__frame"></div>
    <div class="sign__frame-inner"></div>
    <div class="brand">
      <div class="brand__dot"></div>
      <div class="brand__name">BRACKWELL<br>CONSTRUCTION<span class="brand__sub">COMPANY</span></div>
    </div>
    <svg class="banner-art" viewBox="0 0 718 574" aria-hidden="true">
      <path d="M150 300 Q128 330 128 362 L140 362 Q142 330 160 302 Z" fill="var(--navy)"/>
      <path d="M568 300 Q590 330 590 362 L578 362 Q576 330 558 302 Z" fill="var(--navy)"/>
      <path d="M150 530 Q128 500 128 468 L140 468 Q142 500 160 528 Z" fill="var(--navy)"/>
      <path d="M568 530 Q590 500 590 468 L578 468 Q576 500 558 528 Z" fill="var(--navy)"/>
      <polygon points="92,335 640,335 662,400 640,468 92,468 70,400" fill="var(--white)" stroke="var(--navy)" stroke-width="5" stroke-linejoin="round"/>
      <polygon points="60,400 88,392 84,400 88,408" fill="var(--navy)"/>
      <polygon points="672,400 644,392 648,400 644,408" fill="var(--navy)"/>
    </svg>
    <div class="services">
      RESIDENTIAL <span class="joiner">AND</span> COMMERCIAL<br>
      RENOVATIONS <span class="joiner">AND</span> MAINTENANCE
    </div>
  </section>

  <!-- back side -->
  <section class="sign sign--back" aria-label="Sign back">
    <div class="sign__frame"></div>
    <div class="sign__frame-inner"></div>
    <div class="back__tag">LICENSED AND INSURED</div>
    <div class="ribbon ribbon--estimates">FREE ESTIMATES</div>
    <div class="ribbon ribbon--phone">810-555-0142</div>
    <div class="back__web">www.brackwellbuilders.com</div>
    <div class="back__address">Harrow Road<br>Elm Township, Michigan, MI, US 48599 MI</div>
  </section>

</body>
</html>
```